Transport & Storage Company needs a revamp of current card

Would like to keep same colours & basic design but would like to "sharpen" up look of card.

Please remove "The Brisk Haulers"

Please add 1800 418 239 on front & back of card

Please add email address on back of card - colin@bluegatefreight.com.au

I would like our ABN No - 38 214 906 731 on back of card (which currently has logo only). Logo on back of card can be removed if insufficient space.

Please design another card (same as above) but with Maren Ashcombe - 0431 702 548, maren@bluegatefreight.com.au

I do not want cards to look "too busy" so please re-arrange layout of card if necessary.

Target Market(s)

Transport & Storage

Industry/Entity Type

It Company

Contact Information for Business Card

Please refer to attached current business card

Font styles to use
Other font styles liked:
• Tahoma

Requirements
Must have
• Refer to project decsription
Nice to have
Should not have

```html
<!DOCTYPE html>
<html lang="en">
<head>
<meta charset="utf-8">
<title>Bluegate Freight – Business Cards</title>
<link rel="stylesheet" href="https://fonts.googleapis.com/css2?family=PT+Sans:wght@400;700&display=swap">
<style>
  :root {
    --stage: #aeaa86;
    --purple: #763a84;
    --grey: #58585a;
    --white: #ffffff;
    --text-font: "PT Sans", Tahoma, sans-serif;
  }
  * { box-sizing: border-box; margin: 0; padding: 0; }
  html, body { width: 1083px; height: 1200px; overflow: hidden; }
  body { background: var(--stage); font-family: var(--text-font); position: relative; }

  .card {
    position: absolute;
    left: 76px;
    width: 922px;
    height: 539px;
    background: var(--white);
    overflow: hidden;
    box-shadow: 0 4px 14px rgba(0,0,0,0.35);
  }
  .card--front { top: 47px; }
  .card--back { top: 623px; }

  .card__shapes { position: absolute; inset: 0; width: 100%; height: 100%; }

  /* Front */
  .front__name {
    position: absolute; left: 61px; top: 230px;
    color: var(--white); font-weight: 700; font-size: 31px; line-height: 1;
  }
  .front__phones { position: absolute; left: 58px; top: 308px; list-style: none; }
  .front__phone {
    display: flex; align-items: center; gap: 10px;
    color: var(--white); font-size: 25px; line-height: 34px;
  }
  .phone-icon { width: 20px; height: 24px; fill: var(--white); }
  .front__brand {
    position: absolute; left: 512px; top: 180px; width: 345px;
    display: flex; align-items: center; justify-content: center; gap: 12px;
    color: var(--purple); font-weight: 700; font-size: 38px; line-height: 1;
  }
  .brand-mark { width: 22px; height: 22px; background: var(--purple); flex: none; }
  .front__web {
    position: absolute; left: 68px; top: 450px; width: 770px;
    color: var(--purple); font-size: 24px; line-height: 1;
    letter-spacing: 12.4px; white-space: nowrap;
  }

  /* Back */
  .back__brand {
    position: absolute; left: 0; right: 0; top: 120px;
    display: flex; align-items: center; justify-content: center; gap: 18px;
    color: var(--purple); font-weight: 700; font-size: 72px; line-height: 1;
  }
  .back__brand .brand-mark { width: 38px; height: 38px; }
  .back__abn {
    position: absolute; left: 0; right: 0; top: 298px; text-align: center;
    color: var(--purple); font-size: 18px;
  }
  .back__phone-band {
    position: absolute; left: 0; right: 0; top: 348px; height: 57px;
    background: var(--purple); color: var(--white);
    display: flex; align-items: center; justify-content: center;
    font-size: 25px;
  }
  .back__contact-band {
    position: absolute; left: 0; right: 0; top: 408px; bottom: 0;
    background: var(--grey); color: var(--white);
    text-align: center; font-size: 25px; padding-top: 8px;
  }
</style>
</head>
<body>

<section class="card card--front" aria-label="Business card front">
  <svg class="card__shapes" viewBox="0 0 922 539" aria-hidden="true">
    <polygon points="541,0 922,0 922,22 514,60" fill="var(--purple)"/>
    <polygon points="0,119 487,119 311,423 0,423" fill="var(--purple)"/>
    <polygon points="0,522 922,478 922,539 0,539" fill="var(--grey)"/>
  </svg>

  <h1 class="front__name">Colin Harwood</h1>
  <ul class="front__phones">
    <li class="front__phone">
      <svg class="phone-icon" viewBox="0 0 20 24" aria-hidden="true"><path d="M14 1c-6 0-11 5-11 11s5 11 11 11l2-5c-4 0-7-3-7-6s3-6 7-6z"/></svg>
      0452 317 806
    </li>
    <li class="front__phone">
      <svg class="phone-icon" viewBox="0 0 20 24" aria-hidden="true"><path d="M14 1c-6 0-11 5-11 11s5 11 11 11l2-5c-4 0-7-3-7-6s3-6 7-6z"/></svg>
      1800 418 239
    </li>
  </ul>

  <div class="front__brand"><span class="brand-mark" aria-hidden="true"></span>Bluegate Freight</div>
  <p class="front__web">www.bluegatefreight.com.au</p>
</section>

<section class="card card--back" aria-label="Business card back">
  <div class="back__brand"><span class="brand-mark" aria-hidden="true"></span>Bluegate Freight</div>
  <p class="back__abn">ABN No - 38 214 906 731</p>
  <div class="back__phone-band">1800 418 239</div>
  <div class="back__contact-band">colin@bluegatefreight.com.au</div>
</section>

</body>
</html>
```